GearHive.com

Our company, GearHive Inc., is an established business with an extensive worldwide customer base in the Aviation, Aerospace, and Defense Industries.
GearHive Inc, is an e-commerce platform driven by an aviation parts locator. We are looking to totally redo our homepage, log-in page, standard part search page, and results page.
Our current web design is in 800frame and we need it to be updated to a centered 1280 frame. The new design also needs to be easily viewed from any mobile device. The new size needs to accommodate 2-3 advertisements, both vertically and horizontally.
I like clean, simple, crisp lines that can easily be navigated by everyone. Along with Aviation/Aerospace stock photos, I would like to use different shades of blue and grey and accent specific buttons/drop-downs with orange or yellow.
We are also looking for a web designer who also has the ability to cut up the page and turn over to our .NET developers.
Attached are the 4 pages that I would like to start working on. The standard content within these pages need to be incorporated into the new design.
Our current website is www.gearhive.com
Below are some industry websites that I like the color and feel of.
Please use attached pic of corvane T410 as main photo
http://www.stravelcorp.com/
http://www.quillanor.com/en/aerospace.html
http://www.dexavend.com/
http://aerospace.veltrimax.com/

```html
<!DOCTYPE html>
<html lang="en">
<head>
<meta charset="utf-8">
<title>GearHive — Home</title>
<link href="https://fonts.googleapis.com/css2?family=Questrial&family=Roboto+Slab:wght@700&display=swap" rel="stylesheet">
<style>
:root{
  --blue:#0b7ad6;
  --blue-head:#0a6fd0;
  --navy:#1f2b8c;
  --grey-text:#7a7a7a;
  --card-bg:#f5f5f5;
  --footer-bg:#f3f3f3;
  --white:#ffffff;
}
*{margin:0;padding:0;box-sizing:border-box}
html,body{width:848px;height:1200px;overflow:hidden;background:var(--white)}
body{position:relative;font-family:"Questrial",sans-serif;color:var(--grey-text)}
.abs{position:absolute}
.slab{font-family:"Roboto Slab",serif;font-weight:700}

.logo{left:93px;top:8px;font-size:27px;color:var(--blue);letter-spacing:-.5px}
.top-links{right:93px;top:19px;font-size:10px;color:var(--navy);display:flex;gap:10px}
.top-links span.sep{color:var(--navy)}

.main-nav{left:0;top:51px;width:848px;height:51px;background:var(--blue)}
.main-nav ul{list-style:none;position:relative;height:100%}
.main-nav li{position:absolute;top:20px;font-size:10px;color:var(--white);letter-spacing:.2px}

.hero{left:0;top:102px;width:848px;height:312px;background:linear-gradient(160deg,#5f88c2 0%,#7fa3d3 45%,#6f97cc 100%)}
.hero-title{left:352px;top:198px;width:410px;font-size:18px;line-height:24px;color:var(--white);text-transform:uppercase}
.hero-text{left:352px;top:256px;width:410px;font-size:16px;line-height:24px;letter-spacing:1.1px;color:var(--white)}
.btn-outline{border:2px solid var(--white);color:var(--white);display:flex;align-items:center;justify-content:center}
.hero-btn{left:352px;top:342px;width:131px;height:39px;font-size:18px}
.dots{left:704px;top:386px;display:flex;gap:4px}
.dots i{width:10px;height:10px;border-radius:50%;background:var(--white);display:block}
.dots i.on{background:var(--blue)}

.feature{top:440px;width:156px;height:192px;background:var(--card-bg);border-bottom:3px solid var(--blue);text-align:center}
.feature svg{position:absolute;left:42px;top:10px}
.feature h3{position:absolute;top:95px;width:100%;font-size:14.5px;color:var(--blue-head)}
.feature p{position:absolute;top:120px;left:20px;right:20px;font-size:10px;line-height:20px}

.signup{left:93px;top:660px;width:662px;height:82px;background:var(--blue)}
.signup-text{left:22px;top:29px;font-size:14.5px;color:var(--white)}
.signup-btn{left:494px;top:22px;width:143px;height:38px;font-size:17.5px}

.section-head{font-size:18px;color:var(--blue-head);top:765px}
.arrows{top:770px;display:flex;gap:4px}
.arrows i{width:16px;height:13px;background:var(--blue);display:flex;align-items:center;justify-content:center}

.news-img{left:93px;width:57px;height:58px}
.news-title{left:163px;font-size:12.5px;color:var(--blue-head)}
.news-date{left:163px;font-size:9.5px;color:var(--blue)}
.news-text{left:163px;font-size:9.5px;line-height:15.5px}

.testimonial{left:426px;top:802px;width:329px;height:121px;background:#f2f2f2}
.testimonial p{position:absolute;left:24px;top:16px;width:295px;font-size:9.6px;line-height:16px;color:#6e6e6e}
.testimonial .author{position:absolute;left:24px;top:88px;font-size:9.6px;color:var(--blue)}

.site-footer{left:0;top:965px;width:848px;height:178px;background:var(--footer-bg)}
.footer-col{top:22px}
.footer-col h4{font-size:14.5px;color:var(--blue-head);margin-bottom:7px}
.footer-col ul{list-style:none;font-size:9.6px;line-height:16px;color:#888}
.footer-col.contact ul{line-height:18.5px}

.bottom-bar{left:0;top:1143px;width:848px;height:57px;background:var(--blue);color:var(--white);font-size:9.6px}
.bottom-links{left:93px;top:12px;display:flex;gap:11px}
.copyright{left:93px;top:32px}
.social{left:676px;top:19px;display:flex;gap:4px}
.social i{width:17px;height:17px;border-radius:3px;background:#e9eef6;display:block}
</style>
</head>
<body>

<header>
  <div class="abs logo slab">GearHive</div>
  <nav class="abs top-links">
    <span>GEARHIVE MAIN</span><span class="sep">|</span>
    <span>SKYPAGES</span><span class="sep">|</span>
    <span>MESSAGE BOARD</span><span class="sep">|</span>
    <span>LOGIN</span>
  </nav>
</header>

<nav class="abs main-nav">
  <ul>
    <li style="left:94px">HOME</li>
    <li style="left:144px">ABOUT</li>
    <li style="left:198px">MEMBERSHIP</li>
    <li style="left:283px">BUYERS</li>
    <li style="left:342px">SUPPLIERS</li>
    <li style="left:416px">GOVERNMENT DATA</li>
    <li style="left:532px">ADVERTISE</li>
    <li style="left:606px">MEDIA</li>
    <li style="left:658px">FAQ'S</li>
    <li style="left:706px">CONTACT</li>
  </ul>
</nav>

<section class="abs hero" role="img" aria-label="Photo of a passenger jet climbing against a blue sky"></section>
<h1 class="abs hero-title slab">Government Bidding ? Detailed Logistics and Notification</h1>
<p class="abs hero-text">Updated Solicitation Information. Receive e-mail notification when a Government Solicitation matches your inventory !</p>
<div class="abs hero-btn btn-outline slab">More Info</div>
<div class="abs dots"><i class="on"></i><i></i><i></i><i></i></div>

<section>
  <article class="abs feature" style="left:93px">
    <svg width="72" height="72" viewBox="0 0 72 72"><circle cx="36" cy="36" r="35" fill="none" stroke="var(--blue)" stroke-width="2"/><circle cx="36" cy="36" r="31" fill="var(--blue)"/>
      <circle cx="36" cy="34" r="8" fill="none" stroke="#fff" stroke-width="3"/><rect x="32" y="42" width="8" height="6" fill="#fff"/>
      <g stroke="#fff" stroke-width="2.5" stroke-linecap="round"><line x1="36" y1="18" x2="36" y2="21"/><line x1="22" y1="34" x2="25" y2="34"/><line x1="47" y1="34" x2="50" y2="34"/><line x1="26" y1="24" x2="28" y2="26"/><line x1="46" y1="24" x2="44" y2="26"/></g></svg>
    <h3 class="slab">Solutions</h3>
    <p>Lorem ipsum dolor sit amet, assum possim molestie mel debet.</p>
  </article>
  <article class="abs feature" style="left:262px">
    <svg width="72" height="72" viewBox="0 0 72 72"><circle cx="36" cy="36" r="35" fill="none" stroke="var(--blue)" stroke-width="2"/><circle cx="36" cy="36" r="31" fill="var(--blue)"/>
      <g fill="#fff"><circle cx="36" cy="30" r="5"/><path d="M28 44a8 8 0 0 1 16 0z"/><circle cx="26" cy="33" r="4"/><path d="M19 44a7 7 0 0 1 10-6v6z"/><circle cx="46" cy="33" r="4"/><path d="M53 44a7 7 0 0 0-10-6v6z"/></g></svg>
    <h3 class="slab">Our Community</h3>
    <p>Lorem ipsum dolor sit amet, assum possim molestie mel debet.</p>
  </article>
  <article class="abs feature" style="left:430px">
    <svg width="72" height="72" viewBox="0 0 72 72"><circle cx="36" cy="36" r="35" fill="none" stroke="var(--blue)" stroke-width="2"/><circle cx="36" cy="36" r="31" fill="var(--blue)"/>
      <rect x="23" y="23" width="26" height="26" rx="5" fill="#fff"/><path d="M30 29c1-1 3 2 2 3l-1 1c1 3 3 5 6 6l1-1c1-1 4 1 3 2l-1 2c-6 1-12-5-11-11z" fill="var(--blue)"/></svg>
    <h3 class="slab">Industry Connection</h3>
    <p>Lorem ipsum dolor sit amet, assum possim molestie mel debet.</p>
  </article>
  <article class="abs feature" style="left:599px">
    <svg width="72" height="72" viewBox="0 0 72 72"><circle cx="36" cy="36" r="35" fill="none" stroke="var(--blue)" stroke-width="2"/><circle cx="36" cy="36" r="31" fill="var(--blue)"/>
      <g fill="#fff"><circle cx="32" cy="27" r="6"/><path d="M21 47a11 11 0 0 1 18-9v9z"/><circle cx="44" cy="42" r="7"/></g><path d="M44 38v8M40 42h8" stroke="var(--blue)" stroke-width="2"/></svg>
    <h3 class="slab">Member Advantage</h3>
    <p>Lorem ipsum dolor sit amet, assum possim molestie mel debet.</p>
  </article>
</section>

<section class="abs signup">
  <p class="abs signup-text slab">Adversarium neglegentur vis no, nisl quas labore ex eam labore.</p>
  <div class="abs signup-btn btn-outline slab">Signup Now!</div>
</section>

<section>
  <h2 class="abs section-head slab" style="left:93px">Latest News</h2>
  <div class="abs arrows" style="left:331px">
    <i><svg width="6" height="8"><path d="M5 1L2 4l3 3" fill="none" stroke="#fff" stroke-width="1.5"/></svg></i>
    <i><svg width="6" height="8"><path d="M1 1l3 3-3 3" fill="none" stroke="#fff" stroke-width="1.5"/></svg></i>
  </div>
  <div class="abs news-img" style="top:802px;background:linear-gradient(#b9c4cf,#6f7a80)" role="img" aria-label="Photo of a small aircraft on the apron"></div>
  <h3 class="abs news-title slab" style="top:799px">Id soleat cetero accommodare quo</h3>
  <p class="abs news-date" style="top:818px">May 23, 2014</p>
  <p class="abs news-text" style="top:833px">bergren expetendis, his ipsum deserunt te.<br>pro audiam consetetur.</p>

  <div class="abs news-img" style="top:881px;background:linear-gradient(#e8e4df,#5a5550)" role="img" aria-label="Photo of two business people at a laptop"></div>
  <h3 class="abs news-title slab" style="top:878px">Ei aeque omnes nam</h3>
  <p class="abs news-date" style="top:897px">April 15, 2014</p>
  <p class="abs news-text" style="top:912px">bergren expetendis, his ipsum deserunt te.<br>pro audiam consetetur.</p>
</section>

<section>
  <h2 class="abs section-head slab" style="left:426px">Testimonials</h2>
  <div class="abs arrows" style="left:719px">
    <i><svg width="6" height="8"><path d="M5 1L2 4l3 3" fill="none" stroke="#fff" stroke-width="1.5"/></svg></i>
    <i><svg width="6" height="8"><path d="M1 1l3 3-3 3" fill="none" stroke="#fff" stroke-width="1.5"/></svg></i>
  </div>
  <blockquote class="abs testimonial">
    <p>"We have used the new Parts Wanted message board to get new client leads that have lead directly to new business. As a manufacturer, it is helpful to have such a service to see needs that we can help people with in real time.</p>
    <span class="author">- &nbsp;Dan Morell, Tierline Fasteners</span>
  </blockquote>
  <svg class="abs" style="left:724px;top:923px" width="31" height="15"><path d="M0 0h31v0L16 15z" fill="#f2f2f2"/></svg>
</section>

<footer class="abs site-footer">
  <div class="abs footer-col" style="left:93px">
    <h4 class="slab">About Us</h4>
    <ul style="width:145px"><li>Ad sea facilisis assueverit, prima reprimique scribentur usu an. Omnes tation cum cu, at eum dicat feugiat sadipsc-ing. Ne tale lobortis reprimique pro, sed ad amet soleat elo-quentiam.</li></ul>
  </div>
  <div class="abs footer-col" style="left:291px">
    <h4 class="slab">Quick Links</h4>
    <ul><li>Membership</li><li>Buyers</li><li>Suppliers</li><li>Government Data</li><li>Advertise</li><li>Media</li><li>FAQ's</li></ul>
  </div>
  <div class="abs footer-col" style="left:433px">
    <h4 class="slab">How can we help</h4>
    <ul><li>Veltrimax Customer Portal</li><li>Business Aviation Pilots Portal</li><li>Dealer &amp; Service Locator</li><li>Ground Support</li><li>Training Solutions</li><li>Software Support Tools</li><li>Training Solutions</li></ul>
  </div>
  <div class="abs footer-col contact" style="left:618px">
    <h4 class="slab">Contact Us</h4>
    <ul><li>Office : GearHive, Inc.</li><li>412 Harbor Crest Road</li><li>Port Alden, FL 33012</li><li>Phone : (555) 210-4400</li><li>Fax : (555) 210-4495</li><li>Toll Free: (800) 555-0142</li></ul>
  </div>
</footer>

<div class="abs bottom-bar">
  <div class="abs bottom-links"><span>Employment</span><span>|</span><span>Terms</span><span>|</span><span>Contact</span></div>
  <p class="abs copyright">Copyright @2014 GearHive. All rights reserved.</p>
  <div class="abs social" aria-label="Social links"><i></i><i></i><i></i><i></i></div>
</div>

</body>
</html>
```